New Business Card Design Project

Use the flyer uploaded and website www.brightoakbuilders.com for inspiration.
List Our Services on Backside of business cards
Marcus Delling
Harborline Builders Inc.
Licensed General Contractors
858-471-6093

Contact Information for Business Card

Use the flyer uploaded and website www.brightoakbuilders.com for inspiration. List Our Services on Backside of business cards Marcus Delling Harborline Builders Inc. Licensed General Contractors 858-471-6093

```html
<!DOCTYPE html>
<html lang="en">
<head>
<meta charset="utf-8">
<title>Harborline Builders – Business Card</title>
<link rel="stylesheet" href="https://fonts.googleapis.com/css2?family=Cinzel:wght@500;600&family=Montserrat:wght@400;500&display=swap">
<style>
  :root {
    --backdrop: #2b2b2c;
    --card: #1c1c1e;
    --card-edge: #252527;
    --ink: #f4f4f4;
    --rule: #d8d8d8;
  }
  * { box-sizing: border-box; margin: 0; padding: 0; }
  html, body { width: 1200px; height: 900px; overflow: hidden; }
  body {
    background: var(--backdrop);
    display: flex;
    flex-direction: column;
    align-items: center;
    justify-content: center;
    gap: 44px;
    font-family: "Montserrat", Arial, sans-serif;
    color: var(--ink);
  }
  .card {
    position: relative;
    width: 640px;
    height: 366px;
    border-radius: 14px;
    background: linear-gradient(135deg, var(--card) 0%, var(--card-edge) 100%);
  }
  .brand-name {
    font-family: "Cinzel", Georgia, serif;
    font-weight: 500;
    color: var(--ink);
    letter-spacing: 0.04em;
    white-space: nowrap;
  }
  /* Front */
  .card-front { display: flex; align-items: center; justify-content: center; }
  .card-front .brand-name { font-size: 34px; }

  /* Back */
  .card-back .brand-name {
    position: absolute;
    right: 52px;
    top: 112px;
    font-size: 24px;
  }
  .holder {
    position: absolute;
    left: 52px;
    top: 104px;
  }
  .holder-name {
    font-family: "Cinzel", Georgia, serif;
    font-weight: 600;
    font-size: 24px;
    letter-spacing: 0.03em;
  }
  .holder-title {
    font-size: 15px;
    font-weight: 400;
    margin-top: 2px;
  }
  .divider {
    position: absolute;
    left: 52px;
    right: 52px;
    top: 172px;
    height: 1px;
    background: var(--rule);
  }
  .contact-list {
    position: absolute;
    left: 52px;
    top: 190px;
    list-style: none;
    font-size: 15px;
    line-height: 26px;
  }
  .contact-list li { display: flex; align-items: center; gap: 10px; }
  .contact-list svg { width: 13px; height: 13px; fill: var(--ink); flex: none; }
  .contact-list .no-icon { padding-left: 23px; }
  .company-line {
    position: absolute;
    right: 52px;
    bottom: 40px;
    font-size: 15px;
  }
</style>
</head>
<body>
  <section class="card card-front">
    <span class="brand-name">Harborline Builders</span>
  </section>

  <section class="card card-back">
    <span class="brand-name">Harborline Builders</span>

    <div class="holder">
      <h1 class="holder-name">Marcus Delling</h1>
      <p class="holder-title">Licensed General Contractors</p>
    </div>

    <div class="divider"></div>

    <ul class="contact-list">
      <li>
        <svg viewBox="0 0 24 24" aria-hidden="true"><path d="M6.6 10.8a15.1 15.1 0 0 0 6.6 6.6l2.2-2.2a1 1 0 0 1 1-.25 11.4 11.4 0 0 0 3.6.57 1 1 0 0 1 1 1V20a1 1 0 0 1-1 1A17 17 0 0 1 3 4a1 1 0 0 1 1-1h3.5a1 1 0 0 1 1 1c0 1.25.2 2.45.57 3.57a1 1 0 0 1-.25 1z"/></svg>
        <span>858-471-6093</span>
      </li>
      <li>
        <svg viewBox="0 0 24 24" aria-hidden="true"><path d="M2 5h20v14H2z M3.5 6.5 12 13l8.5-6.5" fill="none" stroke="currentColor"/><path d="M2 5h20v2l-10 7L2 7z"/><path d="M2 8.5l10 7 10-7V19H2z"/></svg>
        <span>info@brightoakbuilders.com</span>
      </li>
      <li>
        <svg viewBox="0 0 24 24" aria-hidden="true"><circle cx="12" cy="12" r="10" fill="none" stroke="#f4f4f4" stroke-width="2"/><path d="M2 12h20M12 2c3 3 3 17 0 20M12 2c-3 3-3 17 0 20" fill="none" stroke="#f4f4f4" stroke-width="1.6"/></svg>
        <span>www.brightoakbuilders.com</span>
      </li>
      <li class="no-icon"><span>www.brightoakbuilders.com</span></li>
    </ul>

    <p class="company-line">Harborline Builders Inc.</p>
  </section>
</body>
</html>
```